High-end law practice specializing in closely held business succession planning and complex estates

Solo practitioner whose practice specializes in high-net worth, complex estate planning needs muliple versions of letterhead black and white, please. Letterhead should incorporate slogan, "Protecting your family business is my business," for one and "Complex Estate Planning"; third with no slogan. All for The Law Office of Marcy Lynn Pettibone, PC, 418 Cedar Hollow Ln., Newport News, Virginia 23648, Tel. 757-555-0142 Fax tbd email: marcy@mlplawgroup.example; Marcy Lynn Pettibone, Esq., principal, licensed in VA, NY, DC
Updates

Project Deadline Extended
Reason: My internet service went down and I can only view designs on my smart phone -- it's just too hard to review. So sorry! Working with my ISP now. Please be patient!

Target Market(s)

High net worth clients with complex estate planning needs, family businesses, family farmers, family foresters -- people with unique estate/succession planning needs who need a specialist who understands them.

Industry/Entity Type

Business

Font styles to use
Script

Requirements
Must have
• A high-end look and feel, connoting trustworthiness, special knowledge, and expertise.

```html
<!DOCTYPE html>
<html lang="en">
<head>
<meta charset="utf-8">
<title>Letterhead – The Law Office of Marcy Lynn Pettibone</title>
<link href="https://fonts.googleapis.com/css2?family=Open+Sans:ital,wght@0,400;0,700;0,800;1,700&family=Arimo:wght@400;700&family=Dancing+Script:wght@500&display=swap" rel="stylesheet">
<style>
  :root {
    --backdrop: #d8cfcc;
    --paper: #ffffff;
    --ink: #111111;
    --body-ink: #3a3a3a;
    --band: #000000;
    --band-text: #ffffff;
    --signature: #1c2a9c;
    --rule: #555555;
  }
  html, body {
    margin: 0;
    width: 1200px;
    height: 784px;
    overflow: hidden;
    background: var(--backdrop);
  }
  .letterhead {
    position: absolute;
    left: 320px;
    top: 30px;
    width: 560px;
    height: 724px;
    background: var(--paper);
    box-shadow: 0 2px 10px rgba(0,0,0,0.12);
    box-sizing: border-box;
    padding: 34px 44px 0 48px;
    color: var(--ink);
  }
  .masthead {
    text-align: right;
    font-family: "Open Sans", sans-serif;
  }
  .masthead__slogan {
    font-size: 10px;
    font-weight: 700;
    font-style: italic;
    margin: 0 0 2px;
  }
  .masthead__firm {
    font-size: 20px;
    font-weight: 800;
    letter-spacing: 0.2px;
    margin: 0;
    line-height: 1.1;
    white-space: nowrap;
  }
  .masthead__specialty {
    font-size: 10px;
    font-weight: 700;
    margin: 3px 0 8px;
  }
  .masthead__band {
    background: var(--band);
    color: var(--band-text);
    font-size: 8.5px;
    letter-spacing: 0.3px;
    padding: 5px 44px 5px 10px;
    margin-right: -44px;
    margin-left: 120px;
    white-space: nowrap;
  }
  .letter {
    font-family: "Arimo", sans-serif;
    font-size: 9.5px;
    line-height: 1.3;
    color: var(--body-ink);
    margin-top: 26px;
    width: 440px;
  }
  .letter__salutation {
    font-weight: 700;
    color: var(--ink);
    margin: 0 0 6px;
  }
  .letter p { margin: 0 0 4px; text-align: justify; }
  .closing {
    font-family: "Arimo", sans-serif;
    font-size: 9.5px;
    color: var(--body-ink);
    margin-top: 18px;
  }
  .closing__signature {
    font-family: "Dancing Script", cursive;
    font-size: 22px;
    color: var(--signature);
    margin: 4px 0 2px 10px;
  }
  .closing__name, .closing__company { margin: 0; line-height: 1.3; }
  .contact {
    position: absolute;
    left: 48px;
    right: 44px;
    bottom: 52px;
    border-top: 1px solid var(--rule);
    padding-top: 12px;
    font-family: "Open Sans", sans-serif;
    font-size: 10px;
    color: var(--ink);
    line-height: 1.45;
    white-space: nowrap;
  }
  .contact__address { margin: 0; text-transform: uppercase; }
  .contact__lines { margin: 0; }
  .contact__lines b { font-weight: 700; }
</style>
</head>
<body>
  <main class="letterhead">
    <header class="masthead">
      <p class="masthead__slogan">Protecting Your Family Business is my Business</p>
      <h1 class="masthead__firm">THE LAW OFFICE OF MARCY LYNN PETTIBONE</h1>
      <p class="masthead__specialty">Complex Estate Planning</p>
      <div class="masthead__band">MARCY LYNN PETTIBONE, ESQ. PRINCIPAL, LICENSED IN VA, NY, DC</div>
    </header>

    <section class="letter">
      <p class="letter__salutation">Dear Mr. John,</p>
      <p>Lorem Ipsum is simply dummy text of the printing and typesetting industry. Lorem Ipsum has been the industry's standard dummy text ever since the 1500s, when an unknown printer took a galley of type and scrambled it to make a type specimen book. It has survived not only five centuries, but also the leap into electronic typesetting, remaining essentially unchanged.</p>
      <p>The standard chunk of Lorem Ipsum used since the 1500s is reproduced below for those interested. Sections 1.10.32 and 1.10.33 from "de Finibus Bonorum et Malorum" by Cicero are also reproduced in their exact original form, accompanied by English versions from the 1914 translation by H. Rackham.</p>
      <p>Lorem Ipsum is simply dummy text of the printing and typesetting industry. Lorem Ipsum has been the industry's standard dummy text ever since the 1500s, when an unknown printer took a galley of type and scrambled it to make a type specimen book. It has survived not only five centuries, but also the leap into electronic typesetting, remaining essentially unchanged. It was popularised in the</p>
    </section>

    <section class="closing">
      <p class="closing__name">Sincerely Yours,</p>
      <p class="closing__signature">your name</p>
      <p class="closing__name">Name Last Name</p>
      <p class="closing__company">Company Name</p>
    </section>

    <footer class="contact">
      <p class="contact__address">PC, 418 Cedar Hollow Ln., Newport News, Virginia 23648,</p>
      <p class="contact__lines"><b>T:</b> 757-555-0142 | <b>F:</b> 757-555-0199 | <b>E:</b> marcy@mlplawgroup.example</p>
    </footer>
  </main>
</body>
</html>
```